Verpackungsdesign für Wellness- und Saunaprodukte
Zielgruppe
BaFinn ist ein junges Start-Up, das sich auf Wellness- und Saunaprodukte spezialisiert hat. Unsere Zielgruppe besteht zu beinahe gleichen Teilen aus männlichen und weiblichen Personen zwischen 30 und 60 Jahren. Unsere Produkte befinden sich eher im mittel- bis höherpreisigen Segment, daher streben wir ein hochwertiges Design für unsere Verpackungen an. Unsere Produktpalette reicht von Mentholkristallen, Saunaaufgüssen, bis hin zu Textilien für den Wellnessbereich und soll dementsprechend Menschen ansprechen, die sich einen gewissen Luxus im Alltag auch gönnen.
Aufgabenstellung
Inspiriert von der skandinavischen Sauna Kultur, möchten wir Momente der Erholung und
Entspannung in den Alltag unserer Kunden bringen. Die Geschichte des Saunierens ist eng mit der skandinavischen Kultur verbunden und skandinavische Stilelemente sind zeitgemäß und sprechen ein breites Publikum an. Das Design muss auf Dosen/Tiegel , Karton Verpackungen und Flaschen verschiedener Größen adaptierbar sein (siehe Bild im Anhang).
40g Tiegel(transparent) Höhe 40mm Durchmesser 60mm (ohne Deckel Silber gebürstet)
100g Tiegel(transparent) Höhe 53mm Durchmesser 71mm (ohne Deckel Silber gebürstet)
200g Tiegel(transparent) Höhe 65mm Durchmesser 90mm (ohne Deckel Silber gebürstet)
Karton Verpackung 124,5x49x49mm
Karton Verpackung 100x100x100mm
Flaschenetikett 134x67mm (Braunglas, schwarzer Deckel)
Es soll ein passendes Keyvisual erstellt werden.
Im Anhang sieht man die Verpackungen, Dosen, Flaschen sowie unsere ersten Design Entwürfe (an diese Anordnung der Elemente kann sich der Designer orientieren ). Das Logo bleibt wie gegeben. Das Produkt für die Tiegel soll Mentholkristalle sein.

```html
<!DOCTYPE html>
<html lang="de">
<head>
<meta charset="utf-8">
<title>BaFinn – Nordische Fichte Sauna Aufguss</title>
<link rel="stylesheet" href="https://fonts.googleapis.com/css2?family=Libre+Baskerville:wght@400;700&family=Quicksand:wght@400&display=swap">
<style>
  :root {
    --backdrop: #8b8b8b;
    --carton: #dcdcd8;
    --carton-pattern: #d3d4d0;
    --ink: #7a7a7a;
    --ink-dark: #555555;
    --teal: #1f8a80;
    --teal-deep: #176f67;
  }
  * { margin: 0; padding: 0; box-sizing: border-box; }
  html, body {
    width: 1200px;
    height: 1200px;
    overflow: hidden;
    background: var(--backdrop);
  }
  .canvas {
    position: relative;
    width: 1200px;
    height: 1200px;
  }
  .carton-front {
    position: absolute;
    left: 430px;
    top: 90px;
    width: 340px;
    height: 1020px;
    background: var(--carton);
  }
  .carton-pattern {
    position: absolute;
    left: 12px;
    right: 12px;
    top: 0;
    bottom: 0;
    background: linear-gradient(180deg, var(--carton) 0%, var(--carton-pattern) 50%, var(--carton) 100%);
  }
  .brand {
    position: absolute;
    top: 100px;
    left: 0;
    width: 100%;
    text-align: center;
    font-family: "Quicksand", sans-serif;
    font-weight: 400;
    font-size: 19px;
    color: var(--ink);
    letter-spacing: 0.5px;
  }
  .product-name {
    position: absolute;
    top: 360px;
    left: 0;
    width: 100%;
    text-align: center;
    font-family: "Libre Baskerville", serif;
    font-weight: 700;
    font-size: 23px;
    color: var(--ink);
  }
  .scent-emblem {
    position: absolute;
    top: 672px;
    left: 114px;
    width: 112px;
    height: 112px;
    border-radius: 50%;
    background: radial-gradient(circle at 40% 35%, var(--teal) 0%, var(--teal-deep) 100%);
  }
  .category-label {
    position: absolute;
    top: 828px;
    left: 70px;
    width: 200px;
    height: 42px;
    border: 1px solid var(--ink);
    display: flex;
    font-family: "Libre Baskerville", serif;
    font-weight: 700;
    font-size: 13px;
    color: var(--ink-dark);
  }
  .category-label span {
    display: flex;
    align-items: center;
    justify-content: center;
  }
  .category-label .label-left {
    width: 87px;
    border-right: 1px solid var(--ink);
  }
  .category-label .label-right { flex: 1; }
  .water-lines {
    position: absolute;
    top: 878px;
    left: 70px;
    width: 200px;
    height: 20px;
  }
</style>
</head>
<body>
<div class="canvas">
  <div class="carton-front">
    <div class="carton-pattern" role="img" aria-label="Dezentes helles Muster aus großen skandinavischen Schneekristall-Formen"></div>
    <div class="brand">BaFinn</div>
    <div class="product-name">Nordische Fichte</div>
    <div class="scent-emblem" role="img" aria-label="Türkisfarbenes rundes Emblem mit weißem Schneekristall-Motiv"></div>
    <div class="category-label">
      <span class="label-left">SAUNA</span>
      <span class="label-right">AUFGUSS</span>
    </div>
    <svg class="water-lines" viewBox="0 0 200 20" aria-hidden="true">
      <path d="M0 5 q5 -4 10 0 t10 0 t10 0 t10 0 t10 0 t10 0 t10 0 t10 0 t10 0 t10 0 t10 0 t10 0 t10 0 t10 0 t10 0 t10 0 t10 0 t10 0 t10 0 t10 0" fill="none" stroke="#6f6f6f" stroke-width="1.2"/>
      <path d="M0 15 q5 -4 10 0 t10 0 t10 0 t10 0 t10 0 t10 0 t10 0 t10 0 t10 0 t10 0 t10 0 t10 0 t10 0 t10 0 t10 0 t10 0 t10 0 t10 0 t10 0 t10 0" fill="none" stroke="#6f6f6f" stroke-width="1.2"/>
    </svg>
  </div>
</div>
</body>
</html>
```